Vantiqo custom business card design

Need a authentic, innovative business card design for a new mobile app business. I am uploading a few screen images from our app for you to view. I would like app design theme to match business card design. I can also send logo images.

```html
<!DOCTYPE html>
<html lang="en">
<head>
<meta charset="utf-8">
<title>Vantiqo Business Card</title>
<link rel="stylesheet" href="https://fonts.googleapis.com/css2?family=Work+Sans:wght@400;500;800&display=swap">
<style>
  :root {
    --page-bg: #d8d3ce;
    --card-bg: #2e2c2e;
    --text-main: #e4e0dc;
    --text-soft: #bdb8b3;
    --icon: #a9a39d;
    --accent: #5a2a78;
  }
  * { margin: 0; padding: 0; box-sizing: border-box; }
  html, body {
    width: 1200px;
    height: 1047px;
    overflow: hidden;
    background: var(--page-bg);
    font-family: "Work Sans", Arial, sans-serif;
  }
  .business-card {
    position: absolute;
    left: 100px;
    top: 252px;
    width: 1000px;
    height: 543px;
    background: var(--card-bg);
    border-radius: 26px;
    overflow: hidden;
  }
  .brand-name {
    position: absolute;
    left: 49px;
    top: 34px;
    font-size: 70px;
    font-weight: 800;
    letter-spacing: -1px;
    color: var(--text-main);
    line-height: 1;
  }
  .person {
    position: absolute;
    left: 49px;
    top: 183px;
  }
  .person-name {
    font-size: 34px;
    font-weight: 500;
    color: var(--text-main);
    letter-spacing: 0.5px;
    line-height: 1;
  }
  .person-title {
    margin-top: 10px;
    font-size: 23px;
    font-weight: 400;
    color: var(--text-soft);
    letter-spacing: 0.5px;
  }
  .address {
    position: absolute;
    left: 49px;
    top: 290px;
    font-size: 24px;
    line-height: 37px;
    color: var(--text-soft);
    letter-spacing: 0.6px;
    font-style: normal;
  }
  .contact-list {
    position: absolute;
    left: 49px;
    top: 372px;
    list-style: none;
  }
  .contact-item {
    display: flex;
    align-items: center;
    height: 36px;
    font-size: 25px;
    color: var(--text-soft);
    letter-spacing: 0.6px;
  }
  .contact-icon {
    width: 18px;
    height: 18px;
    margin-right: 17px;
    flex: none;
  }
  .brand-mark {
    position: absolute;
    left: 475px;
    top: 23px;
    width: 490px;
    height: 490px;
    border-radius: 50%;
    background: var(--accent);
    opacity: 0.55;
  }
</style>
</head>
<body>
  <main class="business-card">
    <div class="brand-name">Vantiqo</div>

    <section class="person">
      <div class="person-name">DANIEL REYES</div>
      <div class="person-title">Director</div>
    </section>

    <address class="address">
      1427 Harbor Lane<br>
      Coral Bay, FL 32190
    </address>

    <ul class="contact-list">
      <li class="contact-item">
        <svg class="contact-icon" viewBox="0 0 18 18" aria-hidden="true">
          <rect x="4.5" y="1.5" width="9" height="15" rx="1.5" fill="none" stroke="var(--icon)" stroke-width="1.8"/>
          <line x1="7.5" y1="13.5" x2="10.5" y2="13.5" stroke="var(--icon)" stroke-width="1.6"/>
        </svg>
        (555) 214-7730
      </li>
      <li class="contact-item">
        <svg class="contact-icon" viewBox="0 0 18 18" aria-hidden="true">
          <path d="M4 2 L7 2 L8 6 L6 7.5 Q7.5 11 10.5 12 L12 10 L16 11 L16 14 Q16 16 14 16 Q3 15 2 4 Q2 2 4 2 Z" fill="var(--icon)"/>
        </svg>
        (555) 318-4096
      </li>
      <li class="contact-item">
        <svg class="contact-icon" viewBox="0 0 18 18" aria-hidden="true">
          <rect x="1.5" y="4" width="15" height="10.5" rx="1" fill="none" stroke="var(--icon)" stroke-width="1.6"/>
          <polyline points="1.5,4.5 9,10 16.5,4.5" fill="none" stroke="var(--icon)" stroke-width="1.6"/>
        </svg>
        info@Vantiqo.com
      </li>
      <li class="contact-item">
        <svg class="contact-icon" viewBox="0 0 18 18" aria-hidden="true">
          <circle cx="9" cy="9" r="7.2" fill="none" stroke="var(--icon)" stroke-width="1.5"/>
          <ellipse cx="9" cy="9" rx="3.2" ry="7.2" fill="none" stroke="var(--icon)" stroke-width="1.3"/>
          <line x1="1.8" y1="9" x2="16.2" y2="9" stroke="var(--icon)" stroke-width="1.3"/>
        </svg>
        www.Vantiqo.com
      </li>
    </ul>

    <div class="brand-mark" aria-hidden="true"></div>
  </main>
</body>
</html>
```